Charity Initiative needs a WebPage design

We need a web design for charity initiative by two young guys riding their bikes around Australia to support HarbourLight which helps people with depression and anxiety. Full brief and requirements are attached in the PDF and word document. We have the logo already done and attached. Website will be done in Wordpress and need to get Donations, display current donations, show live Video feed, GPS tracker, Blogs etc and also ability to sell merchandise later

Target Market(s)

Sponsors, Business, Young People

Number of Pages Required

4 page

Font styles to use
Serif
Sans Serif
Decorative
Script

Requirements
Must have
• As per Brief and also Donation status etc
Nice to have
• Please check my logo and read the Bried

```html
<!DOCTYPE html>
<html lang="en">
<head>
<meta charset="utf-8">
<title>Open Road Project — Charity Ride Around Australia</title>
<link rel="stylesheet" href="https://fonts.googleapis.com/css2?family=Open+Sans:wght@400;600;700&display=swap">
<style>
:root{
  --teal:#3aaea8;
  --teal-dark:#2f9791;
  --pink:#e5196a;
  --ink:#333333;
  --muted:#777777;
  --line:#e4e4e4;
  --light:#f4f4f4;
  --footer:#2b2b2b;
  --footer-deep:#1f1f1f;
  --yellow:#f3c21b;
  --white:#ffffff;
}
*{box-sizing:border-box;margin:0;padding:0}
html,body{width:1200px;height:3068px;overflow:hidden}
body{font-family:"Open Sans",Arial,sans-serif;color:var(--ink);background:var(--white);font-size:13px;line-height:1.55}
.wrap{width:1168px;margin:0 auto;position:relative}

/* header */
.site-header{height:128px;position:relative}
.brand{position:absolute;left:120px;top:22px;display:flex;align-items:center;gap:12px}
.brand-mark{width:44px;height:44px;border-radius:50%;background:var(--pink)}
.brand-name{font-size:28px;font-weight:700;color:var(--pink);letter-spacing:-.5px;white-space:nowrap}
.topbar{position:absolute;right:120px;top:14px;display:flex;gap:10px;align-items:center}
.social-dot{width:16px;height:16px;border-radius:50%;background:#bbbbbb}
.lang{border:1px solid var(--line);font-size:11px;padding:2px 8px;color:var(--muted)}
.main-nav{position:absolute;right:120px;top:78px;display:flex;gap:34px;font-size:14px}
.main-nav a{color:var(--ink);text-decoration:none;padding-bottom:6px}
.main-nav a.active{color:var(--pink);border-bottom:2px solid var(--pink)}

/* hero */
.hero{height:412px;position:relative;background:linear-gradient(160deg,#c8b56a 0%,#8a8b3a 35%,#5a6a2e 60%,#8d8a80 100%)}
.hero-callout{position:absolute;right:120px;top:106px;text-align:right}
.hero-callout p{display:inline-block;background:var(--pink);color:var(--white);font-size:23px;font-weight:700;line-height:1.3;padding:10px 18px;width:380px;white-space:normal}
.btn-donate{display:inline-block;margin-top:10px;background:var(--teal);color:var(--white);font-size:22px;font-weight:700;padding:10px 22px;text-decoration:none}
.hero-dots{position:absolute;left:50%;bottom:14px;transform:translateX(-50%);display:flex;gap:8px}
.hero-dots span{width:12px;height:12px;border-radius:50%;background:rgba(255,255,255,.6)}
.hero-dots span.on{background:var(--white)}

/* donation band */
.target-band{height:52px;background:var(--teal);color:var(--white);text-align:center;font-size:19px;font-weight:600;line-height:52px}

/* campaign cards */
.campaigns{height:338px;padding-top:22px}
.campaign-list{display:flex;gap:15px}
.campaign{width:221px;background:var(--white);border:1px solid var(--line)}
.campaign-photo{height:128px;background:linear-gradient(135deg,#6d7a5a,#b9a77a)}
.campaign:nth-child(2) .campaign-photo{background:linear-gradient(135deg,#7a8a9a,#3c4a3a)}
.campaign:nth-child(3) .campaign-photo{background:linear-gradient(135deg,#8a7a5c,#c4a36a)}
.campaign:nth-child(4) .campaign-photo{background:linear-gradient(135deg,#4a5560,#9aa7b0)}
.campaign:nth-child(5) .campaign-photo{background:linear-gradient(135deg,#b08a5a,#6a6050)}
.campaign h3{font-size:12px;font-weight:600;padding:10px 10px 4px;line-height:1.4}
.campaign .amounts{display:flex;justify-content:space-between;font-size:11px;color:var(--pink);padding:8px 10px 2px}
.progress{height:4px;background:var(--line);margin:0 10px}
.progress span{display:block;height:100%;width:48%;background:var(--pink)}
.stats{display:flex;border-top:1px solid var(--line);margin-top:12px}
.stats div{flex:1;text-align:center;padding:8px 0;border-right:1px solid var(--line)}
.stats div:last-child{border-right:0}
.stats b{display:block;font-size:20px;font-weight:400;color:var(--muted)}
.stats small{font-size:10px;color:var(--muted)}

/* intro */
.intro{height:490px;display:flex;align-items:center;position:relative}
.intro-text{width:520px;margin-left:120px}
.intro-text h2{font-size:40px;font-weight:600;line-height:1.2;color:var(--teal)}
.intro-text h2 .pink{color:var(--pink)}
.intro-text p{color:var(--muted);margin:16px 0 20px;font-size:14px;max-width:440px}
.btn-outline{display:inline-block;border:1px solid #cccccc;color:var(--muted);padding:8px 16px;font-size:12px;text-decoration:none}
.video{position:absolute;right:120px;top:40px;width:400px;height:410px;background:linear-gradient(160deg,#8e8e86,#4e4e48 60%,#2e2e2c)}
.video svg{position:absolute;left:50%;top:50%;transform:translate(-50%,-50%)}

/* journal */
.journal{height:460px;position:relative;background:linear-gradient(90deg,var(--pink) 50%,var(--teal) 50%);color:var(--white)}
.journal h2{text-align:center;font-size:30px;font-weight:600;padding-top:28px}
.journal-list{display:flex;gap:60px;justify-content:center;margin-top:28px}
.entry{width:450px}
.entry-photo{height:150px;background:linear-gradient(135deg,#5f7f4a,#a4b88a)}
.entry:nth-child(2) .entry-photo{background:linear-gradient(135deg,#9aa3a8,#5e6b70)}
.entry h3{font-size:13px;font-weight:700;margin:14px 0 8px;line-height:1.4}
.entry p{font-size:12px;opacity:.9}

/* charity */
.charity{height:140px;display:flex;align-items:center}
.charity-brand{margin-left:120px;width:190px;display:flex;align-items:center;gap:10px}
.charity-brand .dot{width:30px;height:30px;background:var(--teal);border-radius:50%}
.charity-brand span{font-size:20px;font-weight:600;color:var(--teal)}
.charity p{width:770px;font-size:12px;color:var(--muted);margin-left:30px}

/* map */
.tracker-map{height:320px;position:relative;background:linear-gradient(135deg,#e9ece4,#dfe6d9 50%,#e8e6dc)}
.tracker-map svg{position:absolute;left:580px;top:128px}

/* blog */
.blog{height:500px;padding-top:30px}
.blog-head{display:flex;justify-content:center;align-items:center;gap:16px}
.blog-head h2{font-size:28px;font-weight:600;color:var(--pink)}
.arrow-btn{width:24px;height:24px;border:1px solid #cccccc;display:flex;align-items:center;justify-content:center}
.blog-list{display:flex;gap:40px;justify-content:center;margin-top:30px}
.post{width:280px}
.post-photo{height:170px;background:linear-gradient(135deg,#c7c08a,#8a8a50)}
.post:nth-child(2) .post-photo{background:linear-gradient(135deg,#6a8a6a,#b4c0a0)}
.post:nth-child(3) .post-photo{background:linear-gradient(135deg,#5a6a80,#a6a08a)}
.post h3{font-size:13px;font-weight:600;color:var(--teal);margin:14px 0 8px;line-height:1.4}
.post p{font-size:12px;color:var(--muted)}
.post a{display:inline-block;margin-top:10px;font-size:11px;font-weight:700;color:var(--ink);text-decoration:none}

/* footer */
.site-footer{height:192px;background:var(--footer);color:#bbbbbb;font-size:11px}
.footer-cols{display:flex;gap:40px;padding:24px 120px 0}
.footer-cols h4{color:var(--yellow);font-size:12px;font-weight:600;margin-bottom:10px}
.col-links{width:110px}
.col-links li{list-style:none;line-height:1.9}
.col-about{width:330px}
.about-row{display:flex;gap:10px}
.about-photo{width:56px;height:56px;flex:none;background:linear-gradient(135deg,#777,#444)}
.col-news{width:200px}
.news-form{display:flex}
.news-form span{flex:1;background:var(--white);color:#999;padding:6px 8px}
.news-form b{background:var(--yellow);width:30px}
.col-connect{width:150px}
.connect-row{display:flex;gap:8px}
.connect-row span{width:24px;height:24px;border-radius:50%;border:1px solid #888}
.copyright{height:36px;background:var(--footer-deep);color:#888;font-size:11px;text-align:center;line-height:36px}
</style>
</head>
<body>

<header class="site-header">
  <div class="brand"><span class="brand-mark"></span><span class="brand-name">Open Road Project</span></div>
  <div class="topbar">
    <span class="social-dot"></span><span class="social-dot"></span><span class="social-dot"></span><span class="social-dot"></span><span class="social-dot"></span>
    <span class="lang">English ▾</span>
  </div>
  <nav class="main-nav">
    <a href="#" class="active">Home</a><a href="#">Journal</a><a href="#">Riders</a><a href="#">Supporters</a><a href="#">Contact</a>
  </nav>
</header>

<section class="hero" role="img" aria-label="Photo of two motorbike riders on a winding road through autumn hills">
  <div class="hero-callout">
    <p>Phasellus nisi est condimentum vitae faucibus</p><br>
    <a href="#" class="btn-donate">DONATE NOW</a>
  </div>
  <div class="hero-dots"><span></span><span class="on"></span><span></span><span></span></div>
</section>

<div class="target-band">Donation Target : Aenean sed quam non sapien faucibus consequat</div>

<section class="campaigns">
  <div class="wrap campaign-list">
    <article class="campaign"><div class="campaign-photo" role="img" aria-label="Photo of riders at sunset"></div><h3>Aenean sed quam non sapien faucibus consequat aliquet mi</h3><div class="amounts"><span>$0</span><span>$5000</span></div><div class="progress"><span></span></div><div class="stats"><div><b>48%</b><small>Support</small></div><div><b>21</b><small>Days Left</small></div><div><b>56</b><small>Backers</small></div></div></article>
    <article class="campaign"><div class="campaign-photo" role="img" aria-label="Photo of a motorbike on a coastal road"></div><h3>Aenean sed quam non sapien faucibus consequat aliquet mi</h3><div class="amounts"><span>$0</span><span>$5000</span></div><div class="progress"><span></span></div><div class="stats"><div><b>48%</b><small>Support</small></div><div><b>21</b><small>Days Left</small></div><div><b>56</b><small>Backers</small></div></div></article>
    <article class="campaign"><div class="campaign-photo" role="img" aria-label="Photo of a rider on a desert track"></div><h3>Aenean sed quam non sapien faucibus consequat aliquet mi</h3><div class="amounts"><span>$0</span><span>$5000</span></div><div class="progress"><span></span></div><div class="stats"><div><b>48%</b><small>Support</small></div><div><b>21</b><small>Days Left</small></div><div><b>56</b><small>Backers</small></div></div></article>
    <article class="campaign"><div class="campaign-photo" role="img" aria-label="Photo of a rider on a mountain pass"></div><h3>Aenean sed quam non sapien faucibus consequat aliquet mi</h3><div class="amounts"><span>$0</span><span>$5000</span></div><div class="progress"><span></span></div><div class="stats"><div><b>48%</b><small>Support</small></div><div><b>21</b><small>Days Left</small></div><div><b>56</b><small>Backers</small></div></div></article>
    <article class="campaign"><div class="campaign-photo" role="img" aria-label="Photo of motorbikes parked at a roadside stop"></div><h3>Aenean sed quam non sapien faucibus consequat aliquet mi</h3><div class="amounts"><span>$0</span><span>$5000</span></div><div class="progress"><span></span></div><div class="stats"><div><b>48%</b><small>Support</small></div><div><b>21</b><small>Days Left</small></div><div><b>56</b><small>Backers</small></div></div></article>
  </div>
</section>

<section class="intro">
  <div class="intro-text">
    <h2>Two mates.<br><span class="pink">Two bikes.</span><br>One long road.</h2>
    <p>Donec ullamcorper nulla non metus auctor fringilla. Vestibulum id ligula porta felis euismod semper. Praesent commodo cursus magna, vel scelerisque nisl consectetur. Fusce dapibus, tellus ac cursus commodo.</p>
    <a href="#" class="btn-outline">Read more</a>
  </div>
  <div class="video" role="img" aria-label="Live video feed of a rider on the road">
    <svg width="70" height="70" viewBox="0 0 70 70"><circle cx="35" cy="35" r="32" fill="none" stroke="#fff" stroke-width="4"/><path d="M28 22 L50 35 L28 48 Z" fill="#fff"/></svg>
  </div>
</section>

<section class="journal">
  <h2>Most Recent Journal Entries</h2>
  <div class="journal-list">
    <article class="entry"><div class="entry-photo" role="img" aria-label="Photo of a rider on a green country road"></div><h3>Donec ullamcorper nulla non metus auctor fringilla. Vestibulum id ligula porta felis euismod semper.</h3><p>Cras mattis consectetur purus sit amet fermentum. Aenean lacinia bibendum nulla sed consectetur. Maecenas faucibus mollis interdum. Nullam quis risus eget urna mollis ornare vel eu leo.</p></article>
    <article class="entry"><div class="entry-photo" role="img" aria-label="Photo of a motorbike mirror on a misty road"></div><h3>Donec ullamcorper nulla non metus auctor fringilla. Vestibulum id ligula porta felis euismod semper.</h3><p>Cras mattis consectetur purus sit amet fermentum. Aenean lacinia bibendum nulla sed consectetur. Maecenas faucibus mollis interdum. Nullam quis risus eget urna mollis ornare vel eu leo.</p></article>
  </div>
</section>

<section class="charity">
  <div class="charity-brand"><span class="dot"></span><span>HarbourLight</span></div>
  <p>Aenean eu leo quam. Pellentesque ornare sem lacinia quam venenatis vestibulum. Donec sed odio dui. Maecenas sed diam eget risus varius blandit sit amet non magna. Nulla vitae elit libero, a pharetra augue. Cras justo odio, dapibus ac facilisis in, egestas eget quam. Vivamus sagittis lacus vel augue laoreet rutrum faucibus dolor auctor. Integer posuere erat a ante venenatis dapibus posuere velit aliquet. Morbi leo risus, porta ac consectetur ac, vestibulum at eros. Curabitur blandit tempus porttitor.</p>
</section>

<section class="tracker-map" role="img" aria-label="GPS tracker map showing the riders' current location">
  <svg width="28" height="40" viewBox="0 0 28 40"><path d="M14 0 C6 0 0 6 0 14 C0 24 14 40 14 40 C14 40 28 24 28 14 C28 6 22 0 14 0 Z" fill="#e5196a"/><circle cx="14" cy="14" r="5" fill="#fff"/></svg>
</section>

<section class="blog">
  <div class="blog-head">
    <span class="arrow-btn"><svg width="8" height="12" viewBox="0 0 8 12"><path d="M7 1 L2 6 L7 11" fill="none" stroke="#999" stroke-width="2"/></svg></span>
    <h2>Blog</h2>
    <span class="arrow-btn"><svg width="8" height="12" viewBox="0 0 8 12"><path d="M1 1 L6 6 L1 11" fill="none" stroke="#999" stroke-width="2"/></svg></span>
  </div>
  <div class="blog-list">
    <article class="post"><div class="post-photo" role="img" aria-label="Photo of a motorbike at a field in golden light"></div><h3>Aenean sed quam non sapien faucibus consequat aliquet amet lorem</h3><p>Donec sed odio dui. Maecenas sed diam eget risus varius blandit sit amet non magna. Nulla vitae elit libero pharetra augue.</p><a href="#">READ MORE</a></article>
    <article class="post"><div class="post-photo" role="img" aria-label="Photo of riders on a forest road"></div><h3>Aenean sed quam non sapien faucibus consequat aliquet amet lorem</h3><p>Donec sed odio dui. Maecenas sed diam eget risus varius blandit sit amet non magna. Nulla vitae elit libero pharetra augue.</p><a href="#">READ MORE</a></article>
    <article class="post"><div class="post-photo" role="img" aria-label="Photo of a rider's gloves and jacket"></div><h3>Aenean sed quam non sapien faucibus consequat aliquet amet lorem</h3><p>Donec sed odio dui. Maecenas sed diam eget risus varius blandit sit amet non magna. Nulla vitae elit libero pharetra augue.</p><a href="#">READ MORE</a></article>
  </div>
</section>

<footer class="site-footer">
  <div class="footer-cols">
    <div class="col-links"><h4>Links</h4><ul><li>Home</li><li>Journal</li><li>Riders</li><li>Supporters</li><li>Contact</li></ul></div>
    <div class="col-about"><h4>About Us</h4><div class="about-row"><div class="about-photo" role="img" aria-label="Photo of the two riders"></div><p>Lorem ipsum dolor sit amet, consectetur adipiscing elit. Nullam id dolor id nibh ultricies vehicula ut id elit. Cum sociis natoque penatibus et magnis dis parturient montes, nascetur ridiculus mus. Donec id elit non mi porta gravida at eget metus.</p></div></div>
    <div class="col-news"><h4>Newsletter Subscribe</h4><div class="news-form"><span>Email Address</span><b></b></div></div>
    <div class="col-connect"><h4>Connect with us</h4><div class="connect-row"><span></span><span></span><span></span><span></span></div></div>
  </div>
</footer>
<div class="copyright">Copyright © 2016 Open Road Project. All rights reserved.</div>

</body>
</html>
```